Solar Company Bussiness Card

I need a 2 sided business card and would like a .psd and any font files for each side of the card. I would like my logo used, it should be attached with the fonts. I'm not opposed to the font colors with the logo being changed.

On the sample design, I'd like the following:

Marcus Dellow
President
Phone: 555-382-9174
www.brightvanepower.example

As I've recently opened in a 2nd market, I'm not sure about an address as I currently have 2 of them. I may actually get separate cards printed, one batch for each address, that's why I need the PSD file.
Updates

I'm very pleased with the response and designs I've received here for my business card. First and foremost, I'd like to thank everyone who took the time to submit a design. There truly are a lot of great designs in the bunch here and I'm having a little difficulty deciding. I will be reaching out to someone in the next day or two here to go to a final design. At this time, I'm not looking for any new concepts. If any of you do logos, I'm looking for a new logo for our sister entity, Dellow Partners, Inc. Thanks, Marcus Dellow

Reason: I'm not looking for any new designs at this point, but extending this deadline in order to give people I've asked a chance to re-submit items.

Industry/Entity Type

Business

```html
<!DOCTYPE html>
<html lang="en">
<head>
<meta charset="utf-8">
<title>Brightvane Power – Business Card</title>
<link rel="stylesheet" href="https://fonts.googleapis.com/css2?family=Exo+2:wght@400;500;600&display=swap">
<style>
  :root{
    --stage:#dcdcdc;
    --card-white:#ffffff;
    --brand-blue:#0b5aa2;
    --ink-dark:#2a2a2a;
    --text-light:#ffffff;
  }
  *{box-sizing:border-box;margin:0;padding:0}
  html,body{width:1200px;height:949px;overflow:hidden}
  body{
    background:var(--stage);
    font-family:"Exo 2",sans-serif;
    display:flex;flex-direction:column;align-items:center;justify-content:center;gap:64px;
  }
  .card{
    width:620px;height:354px;border-radius:22px;overflow:hidden;position:relative;
    background:var(--card-white);
    box-shadow:0 8px 22px rgba(0,0,0,.18);
  }
  .brand{display:flex;align-items:center;gap:14px}
  .brand-mark{width:28px;height:28px;background:var(--brand-blue)}
  .brand-name{font-size:38px;font-weight:600;color:var(--brand-blue);letter-spacing:.5px}

  /* front */
  .card-front{display:flex;flex-direction:column;align-items:center;justify-content:center;gap:34px}
  .card-front .web{font-size:15px;letter-spacing:1.5px;color:var(--ink-dark)}

  /* back */
  .card-back .top{height:120px;display:flex;align-items:center;justify-content:center;padding-left:90px}
  .card-back .band{
    position:absolute;left:0;right:0;top:120px;bottom:0;background:var(--brand-blue);
    color:var(--text-light);padding:30px 34px 30px 38px;
    display:grid;grid-template-columns:1fr 1fr;column-gap:20px;
  }
  .col{display:flex;flex-direction:column;gap:20px;min-width:0}
  .col-right{justify-content:flex-end;gap:16px;padding-bottom:6px}
  .person{display:flex;align-items:baseline;gap:18px;margin-bottom:4px;white-space:nowrap}
  .person .name{font-size:16px;font-weight:500;letter-spacing:2px;text-transform:uppercase}
  .person .role{font-size:11px;letter-spacing:1.5px;text-transform:uppercase}
  .line{display:flex;align-items:center;gap:12px;font-size:13px;letter-spacing:.5px;white-space:nowrap}
  .icon{width:22px;height:22px;flex:none}
  .address{line-height:1.35}
</style>
</head>
<body>

<section class="card card-front" aria-label="Card front">
  <div class="brand">
    <span class="brand-mark"></span>
    <span class="brand-name">Brightvane Power</span>
  </div>
  <p class="web">www.brightvanepower.example</p>
</section>

<section class="card card-back" aria-label="Card back">
  <div class="top">
    <div class="brand">
      <span class="brand-mark"></span>
      <span class="brand-name">Brightvane Power</span>
    </div>
  </div>
  <div class="band">
    <div class="col col-left">
      <div class="person">
        <span class="name">Marcus Dellow</span>
        <span class="role">Founder</span>
      </div>
      <div class="line">
        <svg class="icon" viewBox="0 0 24 24" fill="none" stroke="#fff" stroke-width="1.6"><circle cx="12" cy="12" r="10.5"/><path d="M9 7.5c-1 .6-1.4 1.8-.8 3.2 1 2.3 2.6 4 4.8 5 1.3.6 2.5.2 3.1-.8l-1.7-1.6-1.4.7c-1.1-.6-2-1.5-2.6-2.6l.7-1.4z" fill="#fff" stroke="none"/></svg>
        <span>555-382-9174</span>
      </div>
      <div class="line">
        <svg class="icon" viewBox="0 0 24 24" fill="none" stroke="#fff" stroke-width="1.6"><circle cx="12" cy="12" r="10.5"/><rect x="7" y="8.5" width="10" height="7" fill="#fff" stroke="none"/><path d="M7 8.5l5 4 5-4" stroke="#0b5aa2" stroke-width="1.2"/></svg>
        <span>marcus@brightvanepower.example</span>
      </div>
    </div>
    <div class="col col-right">
      <div class="line">
        <svg class="icon" viewBox="0 0 24 24" fill="none" stroke="#fff" stroke-width="1.6"><circle cx="12" cy="12" r="10.5"/><path d="M12 18s-4-4.2-4-7a4 4 0 0 1 8 0c0 2.8-4 7-4 7z" fill="#fff" stroke="none"/><circle cx="12" cy="11" r="1.5" fill="#0b5aa2" stroke="none"/></svg>
        <span class="address">214 Harlow Street, Suite 6<br>Fenwick</span>
      </div>
      <div class="line">
        <svg class="icon" viewBox="0 0 24 24" fill="none" stroke="#fff" stroke-width="1.4"><circle cx="12" cy="12" r="10.5"/><circle cx="12" cy="12" r="6"/><ellipse cx="12" cy="12" rx="2.6" ry="6"/><path d="M6 12h12"/></svg>
        <span>www.brightvanepower.example</span>
      </div>
    </div>
  </div>
</section>

</body>
</html>
```